Modern & Aesthetic Electrician Sign Design for Work Vehicle

Modern and aesthetic signage design for an electricians work vehicle. Including already designed logo, mobile number, ABN, licensing number and services offered. Preference is black background, symmetric design with logo centred, services offered at bottom of sign in smaller size font. Mobile number readable and big enough to standout without being too large.

Industry/Entity Type

Electrician

Font styles to use
Serif
Sans Serif

Colors
000000
ffffff
ec1f27

Requirements
Must have
• Logo
• Services Offered
• Mobile Number
• ABN
• License Number
• Black background

```html
<!DOCTYPE html>
<html lang="en">
<head>
<meta charset="utf-8">
<title>Ridgeway Electrical – Vehicle Sign</title>
<link rel="stylesheet" href="https://fonts.googleapis.com/css2?family=Exo+2:wght@500;600;700;800&display=swap">
<style>
  :root {
    --black: #000000;
    --white: #ffffff;
    --red: #ec1f27;
    --charcoal: #2b2b2b;
    --page: #f4f4f4;
  }
  html, body {
    margin: 0;
    padding: 0;
    width: 1200px;
    height: 1000px;
    overflow: hidden;
    background: var(--page);
  }
  .canvas {
    position: relative;
    width: 1200px;
    height: 1000px;
    font-family: "Exo 2", sans-serif;
  }
  .sign {
    position: absolute;
    left: 50px;
    top: 242px;
    width: 1100px;
    height: 516px;
    background: var(--black);
    overflow: hidden;
    box-shadow: 0 24px 40px rgba(0,0,0,0.25);
  }
  .sign__registration {
    position: absolute;
    right: 34px;
    top: 30px;
    color: var(--white);
    font-size: 13px;
    font-weight: 600;
    letter-spacing: 1.4px;
    line-height: 17px;
    text-align: right;
  }
  .sign__brand {
    position: absolute;
    left: 0;
    right: 0;
    top: 46px;
    display: flex;
    flex-direction: column;
    align-items: center;
  }
  .brand__ring {
    width: 176px;
    height: 176px;
    border: 10px solid var(--white);
    border-radius: 50%;
    box-sizing: border-box;
  }
  .brand__name {
    margin-top: 30px;
    color: var(--red);
    font-size: 50px;
    font-weight: 800;
    letter-spacing: 2px;
    text-transform: uppercase;
    line-height: 1;
  }
  .sign__services {
    position: absolute;
    left: 0;
    right: 0;
    top: 346px;
    color: var(--white);
    font-size: 22px;
    font-weight: 700;
    letter-spacing: 1.5px;
    line-height: 28px;
  }
  .services__row {
    display: flex;
    justify-content: center;
    align-items: center;
  }
  .services__dot {
    display: inline-block;
    width: 7px;
    height: 7px;
    border-radius: 50%;
    background: var(--red);
    margin: 4px 22px 0;
  }
  .sign__footer {
    position: absolute;
    left: 0;
    bottom: 0;
    width: 1100px;
    height: 78px;
  }
  .sign__phone {
    position: absolute;
    left: 0;
    width: 940px;
    bottom: 0;
    height: 78px;
    display: flex;
    justify-content: center;
    align-items: center;
    gap: 14px;
    color: var(--white);
    font-size: 42px;
    font-weight: 600;
    letter-spacing: 2px;
  }
  .phone__icon {
    width: 38px;
    height: 38px;
    flex: none;
  }
</style>
</head>
<body>
<div class="canvas">
  <section class="sign">
    <div class="sign__registration">
      ABN 00 000 000 000<br>
      LICENSING NO. 000000
    </div>

    <div class="sign__brand">
      <div class="brand__ring"></div>
      <div class="brand__name">Ridgeway Electrical</div>
    </div>

    <div class="sign__services">
      <div class="services__row">
        <span>Service 1</span><span class="services__dot"></span>
        <span>Service 2</span><span class="services__dot"></span>
        <span>Service 3</span><span class="services__dot"></span>
        <span>Service 4</span><span class="services__dot"></span>
        <span>Service 5</span>
      </div>
      <div class="services__row">
        <span>Service 6</span><span class="services__dot"></span>
        <span>Service 7</span><span class="services__dot"></span>
        <span>Service 8</span><span class="services__dot"></span>
        <span>Service 9</span>
      </div>
    </div>

    <svg class="sign__footer" viewBox="0 0 1100 78" aria-hidden="true">
      <polygon class="footer__shade" points="930,30 1100,0 1100,78 820,78" fill="var(--charcoal)"/>
      <polygon class="footer__flash" points="985,36 1100,14 1100,78 1045,78" fill="var(--white)"/>
      <polygon class="footer__band" points="0,0 907,0 944,42 833,78 0,78" fill="var(--red)"/>
    </svg>

    <div class="sign__phone">
      <svg class="phone__icon" viewBox="0 0 38 38" aria-hidden="true">
        <circle cx="19" cy="19" r="19" fill="var(--white)"/>
        <path d="M13.2 9.5c.8-.4 1.7 0 2.1.8l1.7 3.5c.3.7.1 1.5-.4 2l-1.5 1.3c1 2.3 2.8 4.1 5.1 5.1l1.3-1.5c.5-.6 1.3-.7 2-.4l3.5 1.7c.8.4 1.2 1.3.8 2.1l-.9 2.2c-.4 1-1.4 1.6-2.5 1.4C16.8 26.5 11.5 21.2 10.3 13.6c-.2-1.1.4-2.1 1.4-2.5z" fill="var(--red)"/>
      </svg>
      <span class="phone__number">0400 0555 0198</span>
    </div>
  </section>
</div>
</body>
</html>
```